Local fast-growing company in the service sector

We are looking for a modern business card design, which should also appear on our letterheads

Target Market(s)

Private and industrial sectors

Contact Information for Business Card

Vorname Name
Kellberger Str. 18
71498 Bergfelden
Tel.: 07146-839214-0
Name@agentur-kvtl.de

Colors
9d9d9d
919191
aaaaaa

Requirements
Must have
• The logo (file) in silver

```html
<!DOCTYPE html>
<html lang="de">
<head>
<meta charset="utf-8">
<title>KVTL Visitenkarte</title>
<link rel="stylesheet" href="https://fonts.googleapis.com/css2?family=Open+Sans:wght@400;600;700&display=swap">
<style>
  :root {
    --page-bg: #e4e4e4;
    --card-left: #8f8f8f;
    --card-left-dark: #7d7d7d;
    --card-right: #c9c9c9;
    --card-right-light: #dadada;
    --divider: #aaaaaa;
    --divider-light: #eeeeee;
    --text-light: #f4f4f4;
    --text-soft: #e6e6e6;
    --icon-cut: #888888;
    --brand: #4a4a4a;
  }
  * { margin: 0; padding: 0; box-sizing: border-box; }
  html, body { width: 1200px; height: 969px; overflow: hidden; }
  body {
    background: var(--page-bg);
    font-family: "Open Sans", Arial, sans-serif;
    position: relative;
  }
  .business-card {
    position: absolute;
    left: 100px;
    top: 200px;
    width: 1000px;
    height: 570px;
    overflow: hidden;
    box-shadow: 0 8px 30px rgba(0,0,0,0.18);
  }
  .card-shapes { position: absolute; inset: 0; }
  .contact-block {
    position: absolute;
    left: 47px;
    top: 172px;
    color: var(--text-soft);
  }
  .contact-name {
    font-size: 25px;
    font-weight: 700;
    color: var(--text-light);
    letter-spacing: 0.5px;
    margin-bottom: 26px;
  }
  .contact-address {
    font-size: 22px;
    line-height: 33px;
    margin-bottom: 22px;
  }
  .contact-list { list-style: none; font-size: 22px; line-height: 34px; }
  .contact-list li { display: flex; align-items: center; gap: 14px; }
  .contact-icon { width: 18px; height: 18px; fill: var(--text-soft); flex: none; }
  .brand {
    position: absolute;
    left: 525px;
    top: 240px;
    width: 400px;
    display: flex;
    align-items: center;
    justify-content: center;
    gap: 18px;
  }
  .brand-dot {
    width: 64px; height: 64px;
    background: var(--brand);
  }
  .brand-name {
    font-size: 78px;
    font-weight: 700;
    color: var(--brand);
    line-height: 1;
    letter-spacing: 2px;
  }
</style>
</head>
<body>
  <main class="business-card">
    <svg class="card-shapes" width="1000" height="570" viewBox="0 0 1000 570">
      <defs>
        <linearGradient id="leftPanel" x1="0" y1="0" x2="1" y2="1">
          <stop offset="0" stop-color="var(--card-left)"/>
          <stop offset="1" stop-color="var(--card-left-dark)"/>
        </linearGradient>
        <linearGradient id="rightPanel" x1="0" y1="0" x2="1" y2="1">
          <stop offset="0" stop-color="var(--card-right-light)"/>
          <stop offset="1" stop-color="var(--card-right)"/>
        </linearGradient>
      </defs>
      <rect class="panel-right" width="1000" height="570" fill="url(#rightPanel)"/>
      <path class="panel-left" d="M0 0 H655 L400 255 Q378 279 400 303 L640 570 H0 Z" fill="url(#leftPanel)"/>
      <path class="divider" d="M655 0 L400 255 Q378 279 400 303 L640 570" fill="none" stroke="var(--divider-light)" stroke-width="4"/>
      <path class="divider-inner" d="M681 0 L428 255 Q406 279 428 303 L666 570" fill="none" stroke="var(--divider)" stroke-width="3"/>
      <rect width="1000" height="570" fill="none" stroke="var(--divider-light)" stroke-width="2"/>
    </svg>

    <section class="contact-block">
      <h1 class="contact-name">VORNAME NAME</h1>
      <p class="contact-address">Kellberger Str. 18<br>71498 Bergfelden</p>
      <ul class="contact-list">
        <li>
          <svg class="contact-icon" viewBox="0 0 18 18"><path d="M2 4 Q9 0 16 4 L14 7 L11 6 V5 Q9 4 7 5 V6 L4 7 Z M4 8 H14 L16 16 H2 Z"/></svg>
          <span>07146-839214-0</span>
        </li>
        <li>
          <svg class="contact-icon" viewBox="0 0 18 18"><path d="M1 4 H17 V5 L9 10 L1 5 Z M1 7 L9 12 L17 7 V15 H1 Z"/></svg>
          <span>name@agentur-kvtl.de</span>
        </li>
        <li>
          <svg class="contact-icon" viewBox="0 0 18 18"><circle cx="9" cy="9" r="8"/><path d="M1.5 9 H16.5 M9 1 V17 M9 1 Q4 9 9 17 M9 1 Q14 9 9 17" fill="none" stroke="var(--icon-cut)" stroke-width="1.2"/></svg>
          <span>www.agentur-kvtl.de</span>
        </li>
      </ul>
    </section>

    <div class="brand">
      <span class="brand-dot"></span>
      <span class="brand-name">KVTL</span>
    </div>
  </main>
</body>
</html>
```